Blow Dry Bar Business Cards

These cards must be eye catching and modern.
You must be willing to work fast and make changes.

Winner will be offered other projects

Files 1 THIS IS THE STYLE CARDS I AM INTRESTED IN!!!
Please be creative, I am paying for my own eye catching design. I need files to be nexa press ready.

COLORS THAT ARE PAINTED INSIDE MY SHOP:
- - - http://www.quorvelpaint.example/en/explore-colors/painter/color-selector.html?colors=4007-3C

- - - http://www.brandivex.example/color/paint-colors/hidden-corridor-d58-2

I want the business cards sleek and modern if you use the logo please correct imperfections. I added the part that says Blow Dry Bar (see website).
Do not be afraid to separate the blow dryer from the name to make the cards look like the file with the pink elephant.

SHOULD INCLUDE
*Blow Dryer (we are a blow dry bar not a salon we do not cut or color so do not include sheers of any kind)
*BUSINESS NAME: Simply Swept Upward - Blow Dry Bar (PLEASE SEE MY WEBSITE)
* Website: SIMPLYSWEPTUPWARD.EXAMPLE
*Phone number (555) 014-2763
Updates

Nexa press said it can be submitted in JPG

http://www.brandivex.example/color/paint-colors/hidden-corridor-d58-2 http://www.quorvelpaint.example/en/explore-colors/painter/color-selector.html?colors=4007-3C ^^^^ These links will take you to the color paint that is painted inside my shop.

Target Market(s)

AGES 18 - 55 WOMEN
HIGH END MARKET

Industry/Entity Type

Salon

Requirements
Must have
• SEE COLOR EXAMPLE FILE
BLOW DRYER
UNIQUE
I LIKE THE CARD WITH THE PINK ELEPHANT THE BEST
Nice to have
• BE AS CREATIVE AND MODERN AS POSSIBLE DO NOT COPY ANY OF THE CARDS BELOW.
Should not have
• SCISSORS
PINK

```html
<!DOCTYPE html>
<html lang="en">
<head>
<meta charset="utf-8">
<title>Swept Upward Blow Dry Bar – Business Cards</title>
<link rel="stylesheet" href="https://fonts.googleapis.com/css2?family=Roboto+Slab:wght@400&family=Arimo:wght@400&display=swap">
<style>
  :root {
    --canvas-bg: #e9e6e1;
    --card-black: #050505;
    --brand-yellow: #ffcb05;
  }
  * { box-sizing: border-box; margin: 0; padding: 0; }
  html, body {
    width: 1200px;
    height: 1023px;
    overflow: hidden;
    background: var(--canvas-bg);
  }
  .sheet {
    width: 1200px;
    height: 1023px;
    display: flex;
    flex-direction: column;
    align-items: center;
    justify-content: center;
    gap: 40px;
  }
  .card {
    position: relative;
    width: 800px;
    height: 457px;
    background: var(--card-black);
    color: var(--brand-yellow);
    box-shadow: 0 10px 28px rgba(0, 0, 0, 0.25);
  }
  .brand-name {
    font-family: "Roboto Slab", serif;
    font-weight: 400;
    color: var(--brand-yellow);
    white-space: nowrap;
    display: flex;
    align-items: center;
  }
  .brand-dot {
    display: inline-block;
    border-radius: 50%;
    background: var(--brand-yellow);
  }

  /* Front */
  .card-front .brand-name {
    position: absolute;
    left: 64px;
    top: 62px;
    font-size: 74px;
    gap: 22px;
  }
  .card-front .brand-dot { width: 30px; height: 30px; }
  .tagline {
    position: absolute;
    left: 290px;
    top: 172px;
    font-family: "Arimo", sans-serif;
    font-size: 36px;
    letter-spacing: 0.5px;
  }
  .contact {
    position: absolute;
    left: 64px;
    top: 262px;
    font-family: "Arimo", sans-serif;
    font-size: 17px;
    line-height: 34px;
    text-transform: uppercase;
    list-style: none;
  }
  .contact li:nth-child(1) { padding-left: 300px; }
  .contact li:nth-child(2) { padding-left: 264px; }
  .contact li:nth-child(3) { padding-left: 200px; }
  .contact li:nth-child(4) { padding-left: 0; }

  /* Back */
  .card-back .brand-name {
    position: absolute;
    left: 50%;
    top: 50%;
    transform: translate(-50%, -50%);
    font-size: 96px;
    gap: 28px;
  }
  .card-back .brand-dot { width: 40px; height: 40px; }
</style>
</head>
<body>
  <main class="sheet">
    <section class="card card-front" aria-label="Business card front">
      <div class="brand-name">Swept Upward <span class="brand-dot"></span></div>
      <p class="tagline">Blow Dry Bar</p>
      <ul class="contact">
        <li>(555) 014-2763</li>
        <li>SIMPLYSWEPTUPWARD.EXAMPLE</li>
        <li>INFO@SIMPLYSWEPTUPWARD.EXAMPLE</li>
        <li>210 Harbor Bend Drive Suite 4 Lake Marlow, Texas 70014</li>
      </ul>
    </section>

    <section class="card card-back" aria-label="Business card back">
      <div class="brand-name">Swept Upward <span class="brand-dot"></span></div>
    </section>
  </main>
</body>
</html>
```